RWT Fittings Ltd Business Cards

We need a business card with our business logo. We provide window and door installations on high-rises in west coast British Colombia, Canada.

I would like my business information and details on one side of the card, and the other side the company name with logo

Target Market(s)

General Contractors

Industry/Entity Type

Construction

Contact Information for Business Card

one side i want my company name and logo in the dark theme logo that i provided

Requirements
Must have
• Marco Peltieri, 16045518293, RWTFittings@mailbox-demo.com, 1407-5194 Linden Row Burnaby BC, V5H 2K9, Owner & Manager

```html
<!DOCTYPE html>
<html lang="en">
<head>
<meta charset="utf-8">
<title>RWT Fittings Ltd – Business Cards</title>
<link rel="stylesheet" href="https://fonts.googleapis.com/css2?family=Open+Sans:wght@400;600;700&display=swap">
<style>
  :root {
    --backdrop: #3a3a3c;
    --card: #1b1b1d;
    --brand-blue: #29a9e1;
    --accent-grey: #9a9a9a;
    --text-light: #f2f2f2;
  }
  * { margin: 0; padding: 0; box-sizing: border-box; }
  html, body { width: 1200px; height: 780px; overflow: hidden; }
  body {
    background: var(--backdrop);
    font-family: "Open Sans", sans-serif;
    position: relative;
  }
  .card {
    position: absolute;
    width: 540px;
    height: 310px;
    background: var(--card);
    box-shadow: 0 14px 30px rgba(0,0,0,0.45);
    overflow: hidden;
  }
  .card--front { left: 60px; top: 390px; }
  .card--back  { left: 600px; top: 80px; }

  .wordmark {
    display: flex;
    align-items: center;
    gap: 12px;
    color: var(--brand-blue);
    font-weight: 600;
    white-space: nowrap;
  }
  .wordmark__square {
    background: var(--brand-blue);
    flex: none;
  }

  /* front side */
  .card--front .wordmark {
    position: absolute;
    left: 30px;
    top: 62px;
    font-size: 24px;
  }
  .card--front .wordmark__square { width: 22px; height: 22px; }

  .divider {
    position: absolute;
    left: 262px;
    top: 36px;
    width: 1px;
    height: 200px;
    background: var(--brand-blue);
  }
  .contact {
    position: absolute;
    left: 282px;
    top: 40px;
    color: var(--text-light);
  }
  .contact__name {
    color: var(--brand-blue);
    font-weight: 700;
    font-size: 21px;
    letter-spacing: 0.3px;
    text-transform: uppercase;
    line-height: 1.15;
  }
  .contact__role { font-size: 14px; margin-bottom: 10px; }
  .contact__line {
    display: flex;
    align-items: center;
    gap: 7px;
    font-size: 12.5px;
    line-height: 1.65;
  }
  .contact__line svg { width: 11px; height: 11px; flex: none; fill: var(--brand-blue); }
  .contact__address { font-size: 12.5px; line-height: 1.45; margin-top: 4px; }

  .swoosh { position: absolute; left: 0; top: 0; width: 540px; height: 310px; }

  /* back side */
  .card--back .wordmark {
    position: absolute;
    left: 50%;
    top: 50%;
    transform: translate(-50%, -50%);
    font-size: 44px;
    gap: 18px;
  }
  .card--back .wordmark__square { width: 40px; height: 40px; }
</style>
</head>
<body>

  <section class="card card--front" aria-label="Business card, contact side">
    <svg class="swoosh" viewBox="0 0 540 310" aria-hidden="true">
      <path d="M0 292 Q270 196 540 312 L540 310 L0 310 Z" fill="var(--brand-blue)"/>
      <path d="M4 280 Q270 182 538 304" fill="none" stroke="var(--accent-grey)" stroke-width="3"/>
    </svg>

    <div class="wordmark"><span class="wordmark__square"></span>RWT Fittings Ltd</div>

    <div class="divider"></div>

    <div class="contact">
      <p class="contact__name">Marco Peltieri</p>
      <p class="contact__role">Owner &amp; Manager</p>
      <p class="contact__line">
        <svg viewBox="0 0 24 24"><path d="M6.6 10.8a15.1 15.1 0 0 0 6.6 6.6l2.2-2.2a1 1 0 0 1 1-.25 11.4 11.4 0 0 0 3.6.6 1 1 0 0 1 1 1V20a1 1 0 0 1-1 1A17 17 0 0 1 3 4a1 1 0 0 1 1-1h3.5a1 1 0 0 1 1 1 11.4 11.4 0 0 0 .6 3.6 1 1 0 0 1-.25 1z"/></svg>
        16045518293
      </p>
      <p class="contact__line">
        <svg viewBox="0 0 24 24"><path d="M2 5h20v14H2z M2 5l10 8 10-8" /></svg>
        RWTFittings@mailbox-demo.com
      </p>
      <p class="contact__line">
        <svg viewBox="0 0 24 24"><circle cx="12" cy="12" r="10"/></svg>
        www.rwtfittings-demo.com
      </p>
      <p class="contact__address">1407-5194 Linden Row<br>Burnaby BC, V5H 2K9</p>
    </div>
  </section>

  <section class="card card--back" aria-label="Business card, company side">
    <div class="wordmark"><span class="wordmark__square"></span>RWT Fittings Ltd</div>
  </section>

</body>
</html>
```